Vensol Holdings Web Design

Vensol Holdings Limited Shenzhen

This project is a 10 page launch website.
Our client is seeking a contemporary homepage design for a Holdings company. Once we are happy with the homepage design and select designer we will request a secondary page design.

Please see attached company LOGO for an idea of style, it incorporates the traditional Chinese furniture lattice work. The Corvel crest website is one of our clients favorite so we would like to see a similar homepage design to this website.

Use the websites below for reference purpose. The first two are Chinese and the second two are international. We would like to see elements of both but more focus on international design.

http://www.evergrande.com/http://www.taurenfield.com/pub/default.aspx http://www.corvelcrest.com/zh/maldives_lorinhaven/
http://www.quelba-studio.com
http://media-cache-ex0.snapvalu.com/originals/71/a3/19/71a319c5b2d04e8f6a17c3b9e5d0f4a1.jpg

Company Background
VENSOL HOLDINGS, located in Qianhai, China, is a new real-estate project operator, structuring urban-rural real-estate investment and development, and industrial fund investment. The company also invests in supply chain management and supporting infrastructures. To create new spaces and livable cities Vensol Holdings develop win-win strategic partnerships with a number of institutions. Currently cooperating with Tianjing North Lumore, China urban and rural integrated demonstration.

Target Market(s)

B2B property investment. Target market customers are senior level management/decision makers of large corporations. Focusing geographically on the domestic market first and expanding internationally in 2nd and 3rd years.

Industry/Entity Type

Investment

Requirements
Must have
• Since this is a new company, we would like to the website representing growth and power, E.g. like a growing tree.
Should not have
• Low-level vectors such as curency symbols, American dollar.

```html
<!DOCTYPE html>
<html lang="en">
<head>
<meta charset="utf-8">
<title>Vensol Holdings</title>
<link href="https://fonts.googleapis.com/css2?family=Signika:wght@300;400;600&display=swap" rel="stylesheet">
<style>
:root{
  --gold:#f2b821;
  --gold-dark:#d99a0c;
  --gold-text:#d9a010;
  --logo-gold:#c9a24a;
  --ink:#3c3c3c;
  --body:#6b6b6b;
  --dark-1:#2f2f2f;
  --dark-2:#4a4a4a;
  --panel:#f4f4f4;
  --line:#e4e4e4;
  --white:#ffffff;
}
*{margin:0;padding:0;box-sizing:border-box}
html,body{width:730px;height:1200px;overflow:hidden;background:var(--white)}
body{position:relative;font-family:"Signika",sans-serif;color:var(--body)}
.abs{position:absolute}

/* header */
.site-header{position:absolute;left:0;top:0;width:730px;height:78px;background:linear-gradient(#2f2f2f,#4a4a4a)}
.brand{position:absolute;left:84px;top:10px;width:74px;text-align:center}
.brand-mark{display:block;margin:0 auto;width:40px;height:40px;border-radius:50%;background:var(--logo-gold)}
.brand-name{display:block;margin-top:6px;font-size:8px;letter-spacing:.3px;color:var(--logo-gold);font-weight:400;white-space:nowrap}
.search{position:absolute;left:523px;top:19px;width:130px;height:19px;background:var(--white);border:1px solid #ccc;border-radius:2px}
.search svg{position:absolute;right:4px;top:3px}
.main-nav{position:absolute;top:58px;left:0;width:730px;height:20px}
.main-nav a{position:absolute;top:1px;font-size:8.6px;color:#e8e8e8;text-decoration:none;transform:translateX(-50%);white-space:nowrap}
.main-nav a.active{color:var(--gold)}
.nav-underline{position:absolute;left:312px;top:75px;width:39px;height:3px;background:var(--gold)}

/* hero */
.hero{position:absolute;left:0;top:78px;width:730px;height:268px;
  background:linear-gradient(100deg,#8a8a88 0%,#c9a06a 22%,#e6b06e 45%,#d9b084 60%,#6f6a62 75%,#3a3836 100%)}
.avatar{position:absolute;left:110px;top:148px;width:63px;height:64px;background:#fff;border:1px solid #ddd;box-shadow:0 1px 3px rgba(0,0,0,.3);padding:3px}
.avatar span{display:block;width:100%;height:100%;background:linear-gradient(#d8c2b0,#8a6a56)}
.quote{position:absolute;left:184px;top:147px;width:438px;height:75px;background:var(--white);border:1px solid #ddd;box-shadow:0 1px 3px rgba(0,0,0,.3);padding:11px 11px 0 11px}
.quote p{font-size:7.6px;line-height:12.2px;color:#666}
.quote cite{display:block;margin-top:7px;font-style:normal;font-size:8.4px;color:var(--gold-text)}
.hero-arrow{position:absolute;top:205px;width:24px;height:24px}

/* call band */
.call-band{position:absolute;left:0;top:346px;width:730px;height:58px;background:linear-gradient(#3a3a3a,#2a2a2a);border-bottom:2px solid var(--gold)}
.call-band h2{position:absolute;left:79px;top:19px;font-size:15.4px;font-weight:300;color:#f0f0f0}
.btn{position:absolute;display:block;background:linear-gradient(#fbd24a,var(--gold));border:1px solid var(--gold-dark);border-radius:2px;color:#4a3500;font-size:8px;text-align:center;text-decoration:none}
.band-shadow{position:absolute;left:60px;top:406px;width:610px;height:10px;border-radius:50%;background:radial-gradient(ellipse at top,rgba(0,0,0,.22),rgba(0,0,0,0) 70%)}

/* features */
.feature{position:absolute;top:450px;width:194px;text-align:center}
.feature h3{font-size:14px;font-weight:400;color:var(--ink);letter-spacing:.3px}
.feature-icon{display:block;margin:12px auto 0;width:60px;height:60px;border:1px solid #e0c690;border-radius:6px;background:linear-gradient(135deg,#f6efe3 50%,#ece2cf 50%)}
.feature p{margin-top:19px;font-size:7.8px;line-height:11.6px}

/* project */
.project{position:absolute;left:0;top:658px;width:730px;height:238px;background:var(--panel)}
.project-photo{position:absolute;left:79px;top:25px;width:377px;height:173px;border:1px solid #bbb;box-shadow:0 1px 4px rgba(0,0,0,.3);
  background:radial-gradient(ellipse at 45% 55%,#e6e6e6 0%,#9a9a9a 30%,#3a3a3a 80%)}
.project h2{position:absolute;left:469px;top:22px;font-size:17.6px;font-weight:400;color:var(--gold-text)}
.project p{position:absolute;left:469px;width:184px;font-size:7.6px;line-height:11.6px}

/* bottom columns */
.col{position:absolute;top:934px;width:183px}
.col h3{font-size:16px;font-weight:400;color:var(--ink);padding-bottom:6px;border-bottom:1px solid var(--line)}
.col p{font-size:7.6px;line-height:11.6px}
.services{list-style:none;margin-top:9px}
.services li{height:21.5px;font-size:7.6px;border-bottom:1px dotted var(--line);padding-left:15px;position:relative;line-height:13px}
.services li::before{content:"»";position:absolute;left:2px;top:-1px;color:var(--gold);font-size:9px}
.field{position:absolute;left:471px;width:174px;background:linear-gradient(#fafafa,#f0f0f0);border:1px solid #ddd;border-radius:2px;font-size:7px;color:#aaa;padding:6px 11px}

/* footer */
.site-footer{position:absolute;left:0;top:1144px;width:730px;height:56px;background:#333}
.site-footer small{position:absolute;left:81px;top:23px;font-size:7.6px;color:#d0d0d0}
.social{position:absolute;top:19px;width:17px;height:17px;border-radius:2px}
</style>
</head>
<body>

<header class="site-header">
  <div class="brand">
    <span class="brand-mark"></span>
    <span class="brand-name">VENSOL HOLDINGS</span>
  </div>
  <div class="search">
    <svg width="13" height="13" viewBox="0 0 13 13"><circle cx="5" cy="5" r="3.8" fill="none" stroke="#333" stroke-width="1.4"/><line x1="8" y1="8" x2="12" y2="12" stroke="#333" stroke-width="1.8"/></svg>
  </div>
  <nav class="main-nav">
    <a class="active" href="#" style="left:329px">Home</a>
    <a href="#" style="left:373px">About</a>
    <a href="#" style="left:421px">Services</a>
    <a href="#" style="left:469px">Blog</a>
    <a href="#" style="left:510px">News</a>
    <a href="#" style="left:567px">Our Projects</a>
    <a href="#" style="left:631px">Contact Us</a>
  </nav>
  <span class="nav-underline"></span>
</header>

<section class="hero" role="img" aria-label="Blurred photograph of city towers against a warm sunset sky">
</section>
<div class="avatar"><span role="img" aria-label="Portrait photo of the client quoted"></span></div>
<blockquote class="quote">
  <p>Lorem ipsum dolor sit amet, consectetur adipisicing elit, sed do eiusmod tempor incididunt ut labore et doloresaerole magna aliqua. Ut enim ad minim veniam, quis nostrud exercitation ullamco laboris nisi ut aliquip ex ea commodomod consequat. Duis aute irure dolor in reprehenderit in voluptate velit esse cillum dolore eu fugiat nulla pariatur.</p>
  <cite>by Marla Quenby</cite>
</blockquote>
<svg class="hero-arrow" style="left:49px" viewBox="0 0 24 24"><circle cx="12" cy="12" r="12" fill="#333"/><path d="M17 12H7M11 7l-5 5 5 5" fill="none" stroke="#fff" stroke-width="2.4"/></svg>
<svg class="hero-arrow" style="left:655px" viewBox="0 0 24 24"><circle cx="12" cy="12" r="12" fill="#fff"/><path d="M7 12h10M13 7l5 5-5 5" fill="none" stroke="#222" stroke-width="2.4"/></svg>

<section class="call-band">
  <h2>Excepteur sint occaecat cupidatat non proident in deseru.</h2>
  <a class="btn" href="#" style="left:524px;top:19px;width:119px;height:21px;line-height:19px;font-size:8.6px">Find Out More &gt;&gt;</a>
</section>
<div class="band-shadow"></div>

<section class="feature" style="left:73px">
  <h3>RESEARCH</h3>
  <svg class="feature-icon" viewBox="0 0 60 60"><circle cx="30" cy="30" r="13" fill="none" stroke="#2b2620" stroke-width="4"/><path d="M30 23v8h6" fill="none" stroke="#2b2620" stroke-width="3.4"/></svg>
  <p>Donec alsuacnc sit amet eroem sit coning elitufere eu massa. Quisq dipibuque fermen tum. Donec in velit vel ips auctorulvi naProin</p>
  <a class="btn" href="#" style="left:69px;top:155px;width:55px;height:18px;line-height:16px">More &gt;&gt;</a>
</section>
<section class="feature" style="left:268px">
  <h3>STRATEGY</h3>
  <svg class="feature-icon" viewBox="0 0 60 60"><rect x="17" y="20" width="26" height="17" rx="1.5" fill="none" stroke="#2b2620" stroke-width="3"/><path d="M12 40h36v2H12z" fill="#2b2620"/></svg>
  <p>Donec alsuacnc sit amet eroem sit coning elitufere eu massa. Quisq dipibuque fermen tum. Donec in velit vel ips auctorulvi naProin</p>
  <a class="btn" href="#" style="left:70px;top:155px;width:55px;height:18px;line-height:16px">More &gt;&gt;</a>
</section>
<section class="feature" style="left:462px">
  <h3>RESOURCES</h3>
  <svg class="feature-icon" viewBox="0 0 60 60"><g fill="#2b2620" transform="translate(30 30)"><rect x="-3" y="-14" width="6" height="28"/><rect x="-3" y="-14" width="6" height="28" transform="rotate(45)"/><rect x="-3" y="-14" width="6" height="28" transform="rotate(90)"/><rect x="-3" y="-14" width="6" height="28" transform="rotate(135)"/><circle r="10"/></g><circle cx="30" cy="30" r="4" fill="#f1e8d8"/></svg>
  <p>Donec alsuacnc sit amet eroem sit coning elitufere eu massa. Quisq dipibuque fermen tum. Donec in velit vel ips auctorulvi naProin</p>
  <a class="btn" href="#" style="left:70px;top:155px;width:55px;height:18px;line-height:16px">More &gt;&gt;</a>
</section>

<section class="project">
  <div class="project-photo" role="img" aria-label="Black and white photo of a rider on horseback crossing hills against a low sun"></div>
  <svg class="abs" style="left:80px;top:211px" width="16" height="12" viewBox="0 0 16 12"><path d="M6 1L1 6l5 5M10 1l5 5-5 5" fill="none" stroke="#333" stroke-width="2"/></svg>
  <h2>Project Title here...</h2>
  <p style="top:62px">Donec alsuacnc sit amet eroem sit coning elitufere eu massa. Quisq dipibuque fermen tum. Donec ine velit vel ips auctorulvi naProin ullamco.</p>
  <p style="top:108px">Quisq dipibuque fermentum. Donec in veli vel ipm auctorulvinar. Proin ullamcorper urna et felisVesti ibulum iaculnia esoin dictum elementum velitease Fusce euiesoin dictum elementum. Proin ullamcor-per urna et felisVestbulum iaculnia.</p>
  <a class="btn" href="#" style="left:470px;top:180px;width:56px;height:18px;line-height:16px">More &gt;&gt;</a>
</section>

<section class="col" style="left:79px">
  <h3>About Us</h3>
  <p style="margin-top:10px">Donec alsuacnc sit amet eroem sit coning elitufferi eu massa. Quisq dipibuque fermen tum. Donec ine velit vel ips auctorulvi naProin ullamco.</p>
  <p style="margin-top:11px">Quisq dipibuque fermentum. Donec in veli vel ipm auctorulvinar. Proin ullamcorper urna et felisVesti ibulum iaculnia esoin dictum elementum velitease Fusce euiesoin dictum elementum. Proin ullamcor-per urna et felisVestbulum iaculnia.</p>
  <a class="btn" href="#" style="left:0;top:156px;width:57px;height:19px;line-height:17px">More &gt;&gt;</a>
</section>
<section class="col" style="left:274px">
  <h3>Our Services</h3>
  <ul class="services">
    <li>Quisq dipibuque fermentum.</li>
    <li>Donec in veli vel ipm auctorulvinar.</li>
    <li>Proin ullamcorper urna et felisVestibulum</li>
    <li>Aaculnia esoin dictum elementum velitease</li>
    <li>Fusce euiesoin dictum elementum.</li>
    <li style="border-bottom:none">Proin ullamcorper urna et felisVestb</li>
  </ul>
</section>
<section class="col" style="left:470px">
  <h3 style="border-bottom:none">Contact Us</h3>
</section>
<div class="field" style="top:970px;height:21px">Enter your Name....</div>
<div class="field" style="top:1000px;height:21px">Enter your Email...</div>
<div class="field" style="top:1030px;height:50px">Leave a Message...</div>
<a class="btn" href="#" style="left:590px;top:1090px;width:55px;height:19px;line-height:17px;font-size:8.6px">Submit</a>

<footer class="site-footer">
  <small>© 2013 Vensol Holdings. All right reserved.</small>
  <span class="social" style="left:564px;background:#3b5a9a"></span>
  <span class="social" style="left:586px;background:#3eaee0"></span>
  <span class="social" style="left:609px;background:#d2392b"></span>
  <span class="social" style="left:631px;background:#c8281f"></span>
</footer>

</body>
</html>
```